KVM Contracting services . Building and maintenance services, optic fibre installation

Business cards and logo design.I need a logo that I can use on business cards ,workwear and on my vehicles. I would like the KVM to be the main or larger text and contracting services to be the smaller or less important text.I like monograms, modern designs and repeating patterns symbols. I am also a Gemini and my favourite number is 22 so if this can be any inspiration to help with the design. Am thinking of the using German flag colours as a his is my family’s heritage. And the other 2 main colours I wear is black and white.But any ideas are appreciated.I do not need a design that is trade specific but a design that could be used for any business.

Target Market(s)

General public

Contact Information for Business Card

KVM Contracting Services ( front of business card)

(Back of business card)
Darren Holtwick
0451907326
Maintenance services
Optic fibre and data installation

Logo Text

Logo can just be pattern or monogram or incorporate KVM . I like the gemini star sign and the number 22

Colors
ec1f27
000000
fbee3e
ffffff

Requirements
Must have
• Logo and KVM Contracting Services on the front of business card
Nice to have
• Possible use of German flag colours.
• Modern design.
• Design to be able to be used on black or white background as I want to put it on clothing

```html
<!DOCTYPE html>
<html lang="en">
<head>
<meta charset="utf-8">
<title>KVM Contracting Services – Business Cards</title>
<link href="https://fonts.googleapis.com/css2?family=Lato:wght@400;700;900&display=swap" rel="stylesheet">
<style>
  :root {
    --stage: #2b2b2b;
    --card: #151515;
    --red: #ec1f27;
    --yellow: #fbee3e;
    --white: #ffffff;
    --soft-white: #e9e9e9;
  }
  * { box-sizing: border-box; margin: 0; padding: 0; }
  html, body { width: 1200px; height: 900px; overflow: hidden; }
  body {
    background: var(--stage);
    font-family: "Lato", sans-serif;
    position: relative;
  }
  .card {
    position: absolute;
    left: 285px;
    width: 630px;
    height: 360px;
    background: linear-gradient(135deg, #121212 0%, #1b1b1b 60%, #262626 100%);
  }
  .card--front { top: 50px; }
  .card--back { top: 470px; }

  .brand { display: flex; align-items: center; gap: 12px; color: var(--red); font-weight: 900; }
  .brand__square { width: 22px; height: 22px; background: var(--red); flex: none; }
  .brand__text { display: flex; flex-direction: column; line-height: 1; }
  .brand__name { font-size: 96px; letter-spacing: 2px; }
  .brand__tag { font-size: 19px; letter-spacing: 1px; text-transform: uppercase; margin-top: 4px; }

  .card--front .brand { position: absolute; left: 0; right: 0; top: 78px; justify-content: center; }
  .services {
    position: absolute; left: 0; right: 0; top: 248px;
    text-align: center; text-transform: uppercase; letter-spacing: 2px; font-size: 15px; line-height: 1.35;
  }
  .services__maintenance { color: var(--yellow); }
  .services__fibre { color: var(--white); }

  .card--back .brand { position: absolute; left: 40px; top: 120px; }
  .card--back .brand__name { font-size: 82px; }
  .card--back .brand__tag { font-size: 16px; }
  .divider { position: absolute; left: 338px; top: 70px; width: 2px; height: 220px; background: var(--white); }

  .contact { position: absolute; left: 368px; top: 88px; color: var(--soft-white); }
  .contact__name { color: var(--red); font-size: 24px; letter-spacing: 1px; text-transform: uppercase; font-weight: 400; }
  .contact__role { font-size: 16px; margin-bottom: 16px; }
  .contact__address { font-size: 15px; line-height: 1.35; margin-bottom: 10px; font-style: normal; }
  .contact__line { display: flex; align-items: center; gap: 8px; font-size: 15px; line-height: 1.6; }
  .contact__icon { width: 12px; height: 12px; flex: none; }
</style>
</head>
<body>
  <section class="card card--front" aria-label="Business card front">
    <div class="brand">
      <span class="brand__square"></span>
      <span class="brand__text">
        <span class="brand__name">KVM</span>
        <span class="brand__tag">Contracting Services</span>
      </span>
    </div>
    <div class="services">
      <p class="services__maintenance">Maintenance services</p>
      <p class="services__fibre">Optic fibre and data installation</p>
    </div>
  </section>

  <section class="card card--back" aria-label="Business card back">
    <div class="brand">
      <span class="brand__square"></span>
      <span class="brand__text">
        <span class="brand__name">KVM</span>
        <span class="brand__tag">Contracting Services</span>
      </span>
    </div>
    <div class="divider"></div>
    <div class="contact">
      <h1 class="contact__name">Darren Holtwick</h1>
      <p class="contact__role">Director</p>
      <address class="contact__address">18 Linden Row,<br>Fairhaven, FL 32099, USA</address>
      <p class="contact__line">
        <svg class="contact__icon" viewBox="0 0 24 24"><path fill="#ec1f27" d="M6.6 10.8a15 15 0 0 0 6.6 6.6l2.2-2.2a1 1 0 0 1 1-.25 11.4 11.4 0 0 0 3.6.6 1 1 0 0 1 1 1V20a1 1 0 0 1-1 1A17 17 0 0 1 3 4a1 1 0 0 1 1-1h3.5a1 1 0 0 1 1 1c0 1.25.2 2.45.6 3.6a1 1 0 0 1-.25 1z"/></svg>
        0451907326
      </p>
      <p class="contact__line">
        <svg class="contact__icon" viewBox="0 0 24 24"><rect x="2" y="5" width="20" height="14" fill="none" stroke="#ec1f27" stroke-width="2"/><path d="M2 5l10 8 10-8" fill="none" stroke="#ec1f27" stroke-width="2"/></svg>
        hello@kvmbuildservices.com
      </p>
      <p class="contact__line">
        <svg class="contact__icon" viewBox="0 0 24 24"><circle cx="12" cy="12" r="10" fill="none" stroke="#ec1f27" stroke-width="2"/><path d="M2 12h20M12 2c3 3 3 17 0 20M12 2c-3 3-3 17 0 20" fill="none" stroke="#ec1f27" stroke-width="2"/></svg>
        www.kvmbuildservices.com
      </p>
    </div>
  </section>
</body>
</html>
```